Veldmark Supplies Business Card

Professional business card that stand out to our potential customers. Front and back with clean modern design

Industry/Entity Type

Oil and gas

Contact Information for Business Card

Name, address, website , office phone and cell number

Requirements
Must have
• Editable files for each employee

```html
<!DOCTYPE html>
<html lang="en">
<head>
<meta charset="UTF-8">
<title>Veldmark Supplies Business Card</title>
<link href="https://fonts.googleapis.com/css2?family=Montserrat:wght@500;600;800&display=swap" rel="stylesheet">
<style>
  :root {
    --red: #ff0000;
    --cyan: #08b3d6;
    --white: #ffffff;
    --backdrop: #e2e3e2;
  }
  * { box-sizing: border-box; margin: 0; padding: 0; }
  html, body {
    width: 1200px; height: 900px; overflow: hidden;
    background: var(--backdrop);
    font-family: "Montserrat", Arial, sans-serif;
  }
  .card {
    position: absolute; top: 40px;
    width: 466px; height: 815px;
    border-radius: 60px; overflow: hidden;
  }
  .card-front { left: 133px; background: var(--red); }
  .card-back {
    left: 615px;
    background: linear-gradient(var(--white) 0 243px, var(--red) 243px 100%);
  }
  .brand-mark {
    position: absolute; border-radius: 50%;
  }
  .card-front .brand-mark {
    width: 190px; height: 190px; left: 138px; top: 272px;
    background: var(--white);
  }
  .card-back .brand-mark {
    width: 200px; height: 200px; left: 133px; top: 164px;
    background: var(--cyan);
  }
  .brand-name {
    position: absolute; left: 0; right: 0; text-align: center;
    font-weight: 800; text-transform: uppercase; letter-spacing: 1px;
  }
  .card-front .brand-name { top: 512px; font-size: 36px; color: var(--white); }
  .card-back .brand-name { top: 30px; font-size: 32px; color: var(--red); }
  .person-name {
    position: absolute; top: 432px; left: 0; right: 0; text-align: center;
    font-size: 32px; font-weight: 800; color: var(--white); letter-spacing: .5px;
  }
  .person-role {
    position: absolute; top: 476px; left: 88px; right: 88px;
    display: flex; align-items: center; gap: 12px;
    color: var(--white); font-size: 20px; font-weight: 500;
  }
  .person-role::before, .person-role::after {
    content: ""; flex: 1; height: 2px; background: var(--white);
  }
  .contact-icons {
    position: absolute; top: 528px; left: 0; right: 0;
    display: flex; justify-content: center; gap: 20px;
  }
  .contact-icon {
    width: 37px; height: 37px; background: var(--cyan);
    display: flex; align-items: center; justify-content: center;
  }
  .contact-list {
    position: absolute; top: 584px; left: 0; right: 0;
    list-style: none; text-align: center;
    color: var(--white); font-size: 20px; font-weight: 500; line-height: 29.5px;
  }
  .contact-divider {
    position: absolute; top: 717px; left: 117px; right: 117px;
    height: 2px; background: var(--white);
  }
  .address {
    position: absolute; top: 726px; left: 0; right: 0; text-align: center;
    color: var(--white); font-size: 20px; font-weight: 500; line-height: 30px;
    font-style: normal;
  }
</style>
</head>
<body>
  <section class="card card-front" aria-label="Card front">
    <div class="brand-mark"></div>
    <p class="brand-name">Veldmark Supplies</p>
  </section>

  <section class="card card-back" aria-label="Card back">
    <p class="brand-name">Veldmark Supplies</p>
    <div class="brand-mark"></div>
    <h1 class="person-name">DARA WHITLOCK</h1>
    <p class="person-role">President</p>

    <div class="contact-icons">
      <span class="contact-icon" aria-label="Office phone">
        <svg width="24" height="20" viewBox="0 0 24 20" fill="#fff"><path d="M2 6c3-4 17-4 20 0l-1 3h-4l-1-2H8L7 9H3z"/><rect x="5" y="10" width="14" height="8" rx="2"/></svg>
      </span>
      <span class="contact-icon" aria-label="Mobile phone">
        <svg width="14" height="26" viewBox="0 0 14 26" fill="none" stroke="#fff" stroke-width="2"><rect x="1" y="1" width="12" height="24" rx="2"/><circle cx="7" cy="21" r="1" fill="#fff"/></svg>
      </span>
      <span class="contact-icon" aria-label="Email">
        <svg width="26" height="18" viewBox="0 0 26 18" fill="none" stroke="#fff" stroke-width="2"><rect x="1" y="1" width="24" height="16"/><path d="M1 1l12 9 12-9"/></svg>
      </span>
      <span class="contact-icon" aria-label="Website">
        <svg width="24" height="24" viewBox="0 0 24 24" fill="none" stroke="#fff" stroke-width="2"><circle cx="12" cy="12" r="10"/><path d="M2 12h20M12 2c4 4 4 16 0 20M12 2c-4 4-4 16 0 20"/></svg>
      </span>
    </div>

    <ul class="contact-list">
      <li>555-014-2736</li>
      <li>000-000-9999</li>
      <li>info@example-youremail.com</li>
      <li>www.example-yourwebsite.com</li>
    </ul>
    <div class="contact-divider"></div>
    <address class="address">2406 Harlow Ave, Ste<br>100, Brenton, TX 75214</address>
  </section>
</body>
</html>
```